Need Business Card for our Real Estate Business with Sales Executive's Picture

PANTONE 484 C ( RED)

PANTONE 2766 C ( BLUE

Industry/Entity Type

Real Estate

Contact Information for Business Card

Name, Mobile, email, & picture of Person
Agency Phone, address, Web address

Requirements
Must have
• Our Logo Colours, Agent Picture,

```html
<!DOCTYPE html>
<html lang="en">
<head>
<meta charset="utf-8">
<title>Mirada Real Estate – Business Card</title>
<link rel="stylesheet" href="https://fonts.googleapis.com/css2?family=Cinzel:wght@500&family=Josefin+Sans:wght@300;400&display=swap">
<style>
  :root {
    --stage: #e9e9ec;
    --brand-red: #8a1a24;
    --brand-red-deep: #6f121b;
    --navy-deep: #141c4d;
    --navy: #1f2a60;
    --navy-light: #2f3c7a;
    --white: #ffffff;
    --photo-a: #dfe4ee;
    --photo-b: #9aa6c6;
  }
  * { box-sizing: border-box; margin: 0; padding: 0; }
  html, body { width: 1200px; height: 864px; overflow: hidden; }
  body {
    background: var(--stage);
    position: relative;
    font-family: "Josefin Sans", Arial, sans-serif;
    color: var(--white);
  }
  .card {
    position: absolute;
    left: 260px;
    width: 680px;
    height: 389px;
    overflow: hidden;
    border-radius: 4px;
    box-shadow: 0 6px 18px rgba(0,0,0,.18);
  }
  .card--back { top: 28px; background: linear-gradient(160deg, var(--navy-light), var(--navy-deep) 70%); }
  .card--front { top: 447px; background: linear-gradient(170deg, var(--navy-deep) 0%, var(--navy) 45%, var(--navy-light) 100%); }

  /* back */
  .back__red {
    position: absolute; left: 0; top: 0; width: 100%; height: 132px;
    background: linear-gradient(180deg, var(--brand-red), var(--brand-red-deep));
  }
  .back__stripe {
    position: absolute; left: 0; top: 132px; width: 100%; height: 16px;
    background: var(--white);
  }
  .brand-name {
    font-family: "Cinzel", Georgia, serif;
    font-weight: 500;
    color: var(--white);
    letter-spacing: 2px;
    white-space: nowrap;
  }
  .back__brand {
    position: absolute; left: 0; right: 0; top: 250px;
    text-align: center; font-size: 34px;
  }

  /* front */
  .front__brand { position: absolute; left: 42px; top: 48px; font-size: 32px; }
  .front__band {
    position: absolute; left: 0; top: 104px; width: 560px; height: 13px;
    background: var(--white);
  }
  .front__photo {
    position: absolute; left: 484px; top: 40px;
    width: 156px; height: 156px; border-radius: 50%;
    border: 5px solid var(--white);
    box-shadow: 0 0 0 3px var(--navy-deep);
    background: radial-gradient(circle at 50% 35%, var(--photo-a), var(--photo-b));
  }
  .agent-name {
    position: absolute; right: 42px; top: 212px;
    font-family: "Cinzel", Georgia, serif; font-weight: 500;
    font-size: 24px; letter-spacing: 1.5px;
  }
  .contact-list {
    position: absolute; right: 38px; top: 252px;
    list-style: none; text-align: right;
    font-size: 17px; font-weight: 300; letter-spacing: 1px;
  }
  .contact-list li { display: flex; justify-content: flex-end; align-items: center; gap: 12px; height: 24px; }
  .contact-list svg { width: 14px; height: 14px; flex: none; }
  .office-address {
    position: absolute; left: 42px; top: 270px;
    font-size: 17px; font-weight: 300; font-style: normal;
    letter-spacing: 1px; line-height: 22px;
  }
</style>
</head>
<body>
  <section class="card card--back" aria-label="Card back">
    <div class="back__red"></div>
    <div class="back__stripe"></div>
    <div class="brand-name back__brand">Mirada Real Estate</div>
  </section>

  <section class="card card--front" aria-label="Card front">
    <div class="brand-name front__brand">Mirada Real Estate</div>
    <div class="front__band"></div>
    <div class="front__photo" role="img" aria-label="Portrait photo of the sales executive in a blue suit"></div>
    <div class="agent-name">Daniel Reyes</div>
    <ul class="contact-list">
      <li>(09) 555 0142
        <svg viewBox="0 0 24 24" fill="#fff"><path d="M6.6 10.8a15.5 15.5 0 006.6 6.6l2.2-2.2c.3-.3.7-.4 1-.2 1.1.4 2.3.6 3.6.6.6 0 1 .4 1 1V20c0 .6-.4 1-1 1A17 17 0 013 4c0-.6.4-1 1-1h3.5c.6 0 1 .4 1 1 0 1.3.2 2.5.6 3.6.1.3 0 .7-.2 1z"/></svg></li>
      <li>027 555 0187
        <svg viewBox="0 0 24 24" fill="none" stroke="#fff" stroke-width="2"><rect x="6" y="2" width="12" height="20" rx="2"/><line x1="11" y1="18" x2="13" y2="18"/></svg></li>
      <li>daniel@miradarealty.com
        <svg viewBox="0 0 24 24" fill="#fff"><path d="M2 5h20v14H2z"/><path d="M2 5l10 8 10-8" fill="none" stroke="#1f2a60" stroke-width="1.6"/></svg></li>
      <li>www.miradarealty.com
        <svg viewBox="0 0 24 24" fill="none" stroke="#fff" stroke-width="1.8"><circle cx="12" cy="12" r="10"/><ellipse cx="12" cy="12" rx="4.5" ry="10"/><line x1="2" y1="12" x2="22" y2="12"/></svg></li>
    </ul>
    <address class="office-address">2210 Orchard Lane Suite 400<br>Maple Grove, Il 60099</address>
  </section>
</body>
</html>
```